Dental Savings Plan - Raymond Castell DDS

We need a tri-fold brochure and 1 page flyer/poster for Dr. Raymond Castell' dental office located on Maui, Hawaii. We are offering a new "Dental Savings Plan" to patients.
I have included 3 photos, along with the office logo. You do not have to use all photos if you do not want to. We want this to catch the eyes of patients, easy for them to read and understand, and to show them that this is a much better option than dental insurance.
Please use same Hawaiian theme and colors on the office website https://www.brightcoveclinic.com .

Please also include the following to promote this new plan:

Dental Services Include
• Professional Dental Cleanings (2 per benefit year)
• Perio Maintenance Cleanings (3 per benefit year) covered at 80%
• Radiographs as needed (1 set of X-rays per benefit year)
• Doctor Examinations (2 per benefit year)
• Ozone Treatment
• BRISK Amalgam Removal
• Additional limited/emergency exam (1 per benefit year)
• Cosmetic consultation
• 15% discount on all other services (including cosmetic procedures)
• 10% discount on implants and implant crowns

Advantages of the Dental Savings Plan
1. No deductibles
2. No waiting periods
3. No claims to file
4. No frequency limitations or exclusions
5. No yearly maximum benefits
6. No pre-authorization requirements
7. No pre-existing conditions limitations
8. State of the art facility and technology
9. Immediate enrollment
10. Highest quality of care for you and your Ohana

Annual Fee
$399 first family member/individual (equivalent to $33 per month)
$349 second family member (equivalent to $29 per month)
$249 each additional family member (equivalent to $20 per month)

Provisions of the Dental Savings Plan
• May not be combined with insurance plans, discounts or promotions
• This Dental Savings Plan is not an insurance plan, but a payment arrangement provided by Raymond Castell DDS, and is not transferable to any other dental office or dental specialist
• Payment for services are due at the date of service
• This program is for you and is not transferable
• Benefits are provided for one year from the date the plan is purchased
• Must be paid in full when starting the plan
• No refunds will be provided for dues of the plan annual fee under any circumstances, including failure to schedule and maintain appointments
• If Pay Ladder is used to pay for the program and for services then only a 10% discount will be given
• To receive the full 15% discount on restorative treatment, you must schedule the appointment the day it is recommended. Any failed appointment results in the loss of the 15% discount.

Target Market(s)

Dental patients without dental insurance

Industry/Entity Type

Dental Clinic

Requirements
Must have
• My project must have the logo file to identify the dental office, Hawaiian theme, same colors as website, match style of website font, theme and colors, as well as, all the Dental Services, Advantages of the Dental Savings Plan, Annual Fee, and the Provisions of the Dental Savings Plan.

```html
<!DOCTYPE html>
<html lang="en">
<head>
<meta charset="utf-8">
<title>Dental Savings Plan – Raymond Castell DDS</title>
<link rel="stylesheet" href="https://fonts.googleapis.com/css2?family=Encode+Sans+Condensed:wght@400;500;600;700&family=Signika:wght@600;700&display=swap">
<style>
:root{
  --blue:#29a8e0;
  --blue-deep:#1b8fc6;
  --charcoal:#3b3b3d;
  --charcoal-dark:#2c2c2e;
  --paper:#ffffff;
  --mist:#ececec;
  --ink:#2a2a2a;
  --green:#6dbb3c;
  --stage:#dcdcdc;
}
*{box-sizing:border-box;margin:0;padding:0}
html,body{width:1200px;height:1036px;overflow:hidden}
body{background:var(--stage);position:relative;font-family:"Encode Sans Condensed",sans-serif;color:var(--ink)}
.spread{position:absolute;left:30px;width:1140px;height:490px;overflow:hidden;box-shadow:0 4px 14px rgba(0,0,0,.18)}
.spread--outside{top:20px}
.spread--inside{top:526px;background:var(--paper)}
.spread svg.backdrop{position:absolute;inset:0}
.panel{position:absolute;top:0;width:380px;height:490px}
.panel--1{left:0}.panel--2{left:380px}.panel--3{left:760px}

/* outside */
.fee-title{position:absolute;left:96px;top:58px;font-family:"Signika",sans-serif;font-weight:700;font-size:30px;color:var(--ink)}
.fee-list{position:absolute;left:44px;top:104px;list-style:none;font-size:14px;line-height:1.25}
.fee-list li{margin-bottom:12px}
.fee-list strong{font-family:"Signika",sans-serif;font-size:19px;font-weight:700}
.fee-list .monthly{display:block;font-size:13px;color:#555}
.fee-icon{position:absolute;left:164px;top:12px;width:38px;height:38px;border-radius:50%;background:var(--blue)}
.photo{position:absolute}
.photo--patient{left:0;top:300px;width:380px;height:190px;background:linear-gradient(120deg,#f1d3c4 0%,#e9e4e2 45%,#cfe1ec 100%)}
.photo--beach{left:760px;top:0;width:380px;height:490px;background:linear-gradient(180deg,#2f8fd6 0%,#6cc0ef 30%,#21b3d6 52%,#138eb0 66%,#4f8a3a 86%,#7b9b45 100%)}
.brand{position:absolute;left:0;width:380px;top:120px;text-align:center}
.brand-mark{display:inline-block;width:46px;height:46px;border-radius:50%;background:var(--green);margin-bottom:12px}
.brand-name{font-family:"Encode Sans Condensed",sans-serif;font-weight:600;font-size:26px;line-height:1.15;color:var(--green);letter-spacing:.5px}
.brand-tag{font-family:"Encode Sans Condensed",sans-serif;font-weight:600;font-size:26px;line-height:1.15;color:var(--green);display:block}
.contact{position:absolute;left:60px;top:290px;list-style:none;color:#fff;font-size:13px;line-height:1.2}
.contact li{display:flex;align-items:center;gap:10px;margin-bottom:9px}
.contact svg{width:16px;height:16px;flex:none}
.social{position:absolute;left:60px;top:410px;display:flex;gap:14px}
.social span{width:28px;height:28px;border:2px solid #fff;border-radius:3px}
.cover-title{position:absolute;left:800px;top:368px;font-family:"Signika",sans-serif;font-weight:700;font-size:38px;line-height:1.05;color:var(--charcoal-dark)}

/* inside */
.icon-badge{position:absolute;width:66px;height:66px;border-radius:50%;background:var(--blue)}
.icon-badge svg{width:66px;height:66px}
.inside-title{position:absolute;font-family:"Encode Sans Condensed",sans-serif;font-weight:700;font-size:19px;line-height:1.15;color:var(--blue)}
.services{position:absolute;left:24px;top:150px;width:340px;list-style:none;font-size:12px;line-height:1.2}
.services li{position:relative;padding-left:14px;margin-bottom:7px}
.services li::before,.provisions li::before{content:"•";position:absolute;left:0}
.advantages{position:absolute;left:408px;top:168px;width:330px;font-size:12.5px;padding-left:22px}
.advantages li{margin-bottom:11px;padding-left:4px}
.provisions{position:absolute;left:782px;top:112px;width:338px;list-style:none;font-size:11.5px;line-height:1.28}
.provisions li{position:relative;padding-left:12px;margin-bottom:8px}
</style>
</head>
<body>

<section class="spread spread--outside" aria-label="Brochure outside">
  <svg class="backdrop" viewBox="0 0 1140 490" width="1140" height="490" aria-hidden="true">
    <rect x="0" y="0" width="380" height="490" fill="var(--blue)"/>
    <polygon points="18,50 160,26 362,70 362,300 18,300" fill="#7c7c7e"/>
    <polygon points="22,56 160,32 358,76 358,300 22,300" fill="var(--paper)"/>
    <rect x="380" y="0" width="380" height="490" fill="var(--charcoal)"/>
    <polygon points="380,0 760,0 760,22 560,60" fill="var(--blue)"/>
    <polygon points="380,490 380,440 620,490" fill="var(--blue)"/>
  </svg>

  <div class="panel panel--1">
    <span class="fee-icon"></span>
    <h2 class="fee-title">Annual Fee</h2>
    <ul class="fee-list">
      <li><strong>$399</strong> first family member/individual<span class="monthly">(equivalent to $33 per month)</span></li>
      <li><strong>$349</strong> second family member<span class="monthly">(equivalent to $29 per month)</span></li>
      <li><strong>$249</strong> each additional family member<span class="monthly">(equivalent to $20 per month)</span></li>
    </ul>
    <div class="photo photo--patient" role="img" aria-label="Photo of a patient receiving a dental check-up"></div>
  </div>

  <div class="panel panel--2">
    <div class="brand">
      <span class="brand-mark"></span>
      <div class="brand-name">Raymond Castell DDS</div>
      <span class="brand-tag">Smiles by the Shore</span>
    </div>
    <ul class="contact">
      <li><svg viewBox="0 0 16 16"><circle cx="8" cy="8" r="7" fill="none" stroke="#fff"/><path d="M5 4.5l1.5-.5 1 2-1 .8a5 5 0 0 0 2.7 2.7l.8-1 2 1-.5 1.5C8 11.5 4.5 8 5 4.5z" fill="#fff"/></svg>808-555-0142</li>
      <li><svg viewBox="0 0 16 16"><circle cx="8" cy="8" r="7" fill="none" stroke="#fff"/><rect x="4" y="5.5" width="8" height="5.5" fill="none" stroke="#fff"/><path d="M4 5.5l4 3 4-3" fill="none" stroke="#fff"/></svg>hello@brightcoveclinic.com</li>
      <li><svg viewBox="0 0 16 16"><circle cx="8" cy="8" r="7" fill="none" stroke="#fff"/><circle cx="8" cy="8" r="3.5" fill="none" stroke="#fff"/><path d="M4.5 8h7M8 4.5v7" stroke="#fff"/></svg>www.brightcoveclinic.com</li>
      <li><svg viewBox="0 0 16 16"><circle cx="8" cy="8" r="7" fill="none" stroke="#fff"/><path d="M8 12.5S5 9 5 7a3 3 0 0 1 6 0c0 2-3 5.5-3 5.5z" fill="#fff"/></svg>1450 Makai Shore Rd # 118, Kihei, HI 96753</li>
    </ul>
    <div class="social" aria-hidden="true"><span></span><span></span><span></span></div>
  </div>

  <div class="photo photo--beach" role="img" aria-label="Photo of a palm tree over a turquoise Hawaiian sea"></div>
  <h1 class="cover-title">Dental<br>Savings Plan</h1>
</section>

<section class="spread spread--inside" aria-label="Brochure inside">
  <svg class="backdrop" viewBox="0 0 1140 490" width="1140" height="490" aria-hidden="true">
    <defs>
      <linearGradient id="foldShade" x1="0" x2="1">
        <stop offset="0" stop-color="#e2e2e2"/><stop offset="1" stop-color="#f7f7f7"/>
      </linearGradient>
    </defs>
    <rect x="380" y="0" width="380" height="490" fill="url(#foldShade)"/>
    <polygon points="0,0 380,0 380,10 40,30 0,110" fill="var(--blue)"/>
    <polygon points="28,30 40,24 20,120 14,118" fill="#7c7c7e"/>
    <polygon points="380,0 760,0 760,6 560,40 380,90" fill="var(--blue)"/>
    <polygon points="560,40 760,6 760,16" fill="var(--charcoal)"/>
    <polygon points="0,470 1140,470 1140,490 0,490" fill="var(--charcoal)"/>
    <polygon points="760,470 1140,420 1140,470" fill="var(--charcoal)"/>
    <line x1="380" y1="0" x2="380" y2="490" stroke="#d4d4d4"/>
    <line x1="760" y1="0" x2="760" y2="490" stroke="#d4d4d4"/>
  </svg>

  <div class="icon-badge" style="left:42px;top:48px">
    <svg viewBox="0 0 66 66" aria-hidden="true"><g fill="none" stroke="#fff" stroke-width="2"><path d="M20 20v18h22l6 8"/><path d="M20 38l-4 10h26"/><circle cx="44" cy="22" r="4"/></g></svg>
  </div>
  <h2 class="inside-title" style="left:22px;top:118px">Dental Services Include</h2>
  <ul class="services">
    <li>Professional Dental Cleanings<br>(2 per benefit year)</li>
    <li>Perio Maintenance Cleanings<br>(3 per benefit year) covered at 80%</li>
    <li>Radiographs as needed<br>(1 set of X-rays per benefit year)</li>
    <li>Doctor Examinations<br>(2 per benefit year)</li>
    <li>Ozone Treatment</li>
    <li>BRISK Amalgam Removal</li>
    <li>Additional limited/emergency exam<br>(1 per benefit year)</li>
    <li>Cosmetic consultation</li>
    <li>15% discount on all other services<br>(including cosmetic procedures)</li>
    <li>10% discount on implants and implant crowns</li>
  </ul>

  <div class="icon-badge" style="left:636px;top:42px">
    <svg viewBox="0 0 66 66" aria-hidden="true"><path d="M22 18c4-3 8 0 11 0s7-3 11 0c4 4 2 12 0 16l-3 16c-1 3-4 3-4 0l-2-10c-1-3-3-3-4 0l-2 10c0 3-3 3-4 0l-3-16c-2-4-4-12 0-16z" fill="none" stroke="#fff" stroke-width="2"/></svg>
  </div>
  <h2 class="inside-title" style="left:404px;top:112px">Advantages of the<br>Dental Savings Plan</h2>
  <ol class="advantages">
    <li>No deductibles</li>
    <li>No waiting periods</li>
    <li>No claims to file</li>
    <li>No frequency limitations or exclusions</li>
    <li>No yearly maximum benefits</li>
    <li>No pre-authorization requirements</li>
    <li>No pre-existing conditions limitations</li>
    <li>State of the art facility and technology</li>
    <li>Immediate enrollment</li>
    <li>Highest quality of care for you and your Ohana</li>
  </ol>

  <div class="icon-badge" style="left:1060px;top:22px">
    <svg viewBox="0 0 66 66" aria-hidden="true"><g fill="none" stroke="#fff" stroke-width="2"><path d="M20 18c4-3 8 0 11 0s7-3 11 0c4 4 2 12 0 16l-3 16c-1 3-4 3-4 0l-2-10c-1-3-3-3-4 0l-2 10c0 3-3 3-4 0l-3-16c-2-4-4-12 0-16z"/><circle cx="38" cy="32" r="6"/><path d="M42 37l7 8"/></g></svg>
  </div>
  <h2 class="inside-title" style="left:784px;top:26px">Provisions<br>of the Dental<br>Savings Plan</h2>
  <ul class="provisions">
    <li>May not be combined with insurance plans, discounts or promotions</li>
    <li>This Dental Savings Plan is not an insurance plan, but a payment arrangement provided by Raymond Castell DDS, and is not transferable to any other dental office or dental specialist</li>
    <li>Payment for services are due at the date of service</li>
    <li>This program is for you and is not transferable</li>
    <li>Benefits are provided for one year from the date the plan is purchased</li>
    <li>Must be paid in full when starting the plan</li>
    <li>No refunds will be provided for dues of the plan annual fee under any circumstances, including failure to schedule and maintain appointments</li>
    <li>If Pay Ladder is used to pay for the program and for services then only a 10% discount will be given</li>
    <li>To receive the full 15% discount on restorative treatment, you must schedule the appointment the day it is recommended. Any failed appointment results in the loss of the 15% discount.</li>
  </ul>
</section>

</body>
</html>
```